Modern business card design for professional copywriter

I'd like a business card design that I can use to have my cards printed out by quillprint.com as a squared corners business card (see artwork and design guidelines here: https://help.quillprint.com/hc/en-gb/sections/200570950-QUILL-Product-Templates)

The design should be clean and modern and reflect the colours, tone and branding on my website: https://tessavorrin.com.au

Target Market(s)

Professionals, B2B small business owners

Industry/Entity Type

Business

Contact Information for Business Card

Tessa Vorrin
m: 0468 905 327
e: tessa@tessavorrin.com.au
w: tessavorrin.com.au

Font styles to use
Sans Serif

Requirements
Must have
• Tagline: "Smart copywriting for clever business people"
• Brand colours: fd8000, 009984, 666666 and black
Nice to have

```html
<!DOCTYPE html>
<html lang="en">
<head>
<meta charset="utf-8">
<title>Tessa Vorrin – Business Card</title>
<link rel="stylesheet" href="https://fonts.googleapis.com/css2?family=Open+Sans:wght@400;600;700&display=swap">
<style>
  :root {
    --orange: #f28322;
    --charcoal: #3d3f3f;
    --ink: #111111;
    --slate: #555758;
    --white: #ffffff;
    --backdrop: #ececec;
  }
  * { box-sizing: border-box; margin: 0; padding: 0; }
  html, body {
    width: 1200px;
    height: 533px;
    overflow: hidden;
    background: var(--backdrop);
    font-family: "Open Sans", Arial, sans-serif;
  }
  .stage {
    position: relative;
    width: 1200px;
    height: 533px;
  }
  .card {
    position: absolute;
    top: 111px;
    width: 547px;
    height: 311px;
    overflow: hidden;
  }
  /* Front */
  .card--front {
    left: 40px;
    background: var(--charcoal);
  }
  .band {
    position: absolute;
    left: 0;
    width: 100%;
  }
  .card--front .band--top { top: 0; height: 37px; background: var(--orange); }
  .card--front .band--bottom { bottom: 0; height: 39px; background: var(--orange); }

  .brand-mark {
    position: absolute;
    left: 62px;
    top: 137px;
    display: flex;
    align-items: center;
    gap: 8px;
  }
  .brand-mark__dot {
    width: 10px;
    height: 10px;
    border-radius: 50%;
    background: var(--orange);
  }
  .brand-mark__name {
    font-size: 22px;
    font-weight: 600;
    color: var(--orange);
    letter-spacing: 0.2px;
  }

  .divider {
    position: absolute;
    left: 311px;
    top: 101px;
    width: 1px;
    height: 120px;
    background: var(--orange);
  }
  .identity {
    position: absolute;
    left: 351px;
    top: 60px;
  }
  .identity__name {
    font-size: 10.5px;
    font-weight: 700;
    letter-spacing: 0.4px;
    color: var(--ink);
    text-transform: uppercase;
    line-height: 1.2;
  }
  .identity__surname { color: var(--orange); }
  .identity__role {
    font-size: 7px;
    color: var(--ink);
    letter-spacing: 0.3px;
    text-transform: uppercase;
  }
  .contacts {
    position: absolute;
    left: 344px;
    top: 110px;
    list-style: none;
  }
  .contacts__item {
    display: flex;
    align-items: center;
    height: 14px;
    margin-bottom: 25px;
  }
  .contacts__badge {
    width: 14px;
    height: 14px;
    border-radius: 50%;
    background: var(--white);
    color: var(--orange);
    font-size: 7px;
    font-weight: 700;
    display: flex;
    align-items: center;
    justify-content: center;
    margin-right: 19px;
  }
  .contacts__text {
    font-size: 8.5px;
    color: var(--orange);
    letter-spacing: 0.3px;
    text-transform: uppercase;
  }

  /* Back */
  .card--back {
    left: 613px;
    background: var(--orange);
  }
  .card--back .band--bottom { bottom: 0; height: 39px; background: var(--charcoal); }
  .back-brand {
    position: absolute;
    left: 0;
    top: 104px;
    width: 100%;
    text-align: center;
  }
  .back-brand__name {
    font-size: 58px;
    font-weight: 600;
    color: var(--slate);
    line-height: 1;
    letter-spacing: -0.5px;
  }
  .tagline {
    position: absolute;
    left: 0;
    top: 198px;
    width: 100%;
    text-align: center;
    font-size: 8px;
    font-weight: 600;
    letter-spacing: 0.4px;
    color: var(--slate);
    text-transform: uppercase;
  }
</style>
</head>
<body>
<main class="stage">
  <section class="card card--front" aria-label="Business card front">
    <div class="band band--top"></div>

    <div class="brand-mark">
      <span class="brand-mark__dot"></span>
      <span class="brand-mark__name">Tessa Vorrin</span>
    </div>

    <div class="divider"></div>

    <div class="identity">
      <p class="identity__name">Tessa <span class="identity__surname">Vorrin</span></p>
      <p class="identity__role">Copywriter</p>
    </div>

    <ul class="contacts">
      <li class="contacts__item"><span class="contacts__badge">M</span><span class="contacts__text">0468 905 327</span></li>
      <li class="contacts__item"><span class="contacts__badge">E</span><span class="contacts__text">tessa@tessavorrin.com.au</span></li>
      <li class="contacts__item"><span class="contacts__badge">W</span><span class="contacts__text">tessavorrin.com.au</span></li>
    </ul>

    <div class="band band--bottom"></div>
  </section>

  <section class="card card--back" aria-label="Business card back">
    <div class="back-brand">
      <span class="back-brand__name">Tessa Vorrin</span>
    </div>
    <p class="tagline">Smart copywriting for clever business people</p>
    <div class="band band--bottom"></div>
  </section>
</main>
</body>
</html>
```